Quiet Harbor Prints gallery website

I need a Website for a gallery with a shopify integration or maybe even better also compatible with squarespace.
the website should have following riders: Künstler, Veranstaltungen, Shop, About Us.
some nice examples for inspiration of the website architecture are:
https://www.lindwerkraum.com/
https://www.plattenbau-salon.com/de/
https://moorlichtraum.de/
It should be easy for us to make adaptations and fill the website with new content.
Attached there is the CI an logo for the brand.
Target Market(s)
Art Collectors,
Industry/Entity Type
artgallery
Coding
Coded - Design and coding required
Number of Pages Required
3 page
Font styles to use
Look and feel

```html
<!DOCTYPE html>
<html lang="de">
<head>
<meta charset="utf-8">
<title>Quiet Harbor Prints</title>
<link rel="stylesheet" href="https://fonts.googleapis.com/css2?family=Fira+Sans:wght@400;500;600&family=Montserrat:wght@500&family=Poppins:wght@400&display=swap">
<style>
  :root {
    --red: #c0161f;
    --ink: #222222;
    --text: #3a3a3a;
    --white: #ffffff;
    --black: #0a0a0a;
    --head: "Fira Sans", sans-serif;
    --body: "Poppins", sans-serif;
    --nav: "Montserrat", sans-serif;
  }
  * { margin: 0; padding: 0; box-sizing: border-box; }
  html, body { width: 1200px; height: 2381px; overflow: hidden; background: var(--white); }
  .page { position: relative; width: 1200px; height: 2381px; }

  .site-header { position: absolute; left: 0; top: 0; width: 1200px; height: 135px; }
  .brand { position: absolute; left: 118px; top: 82px; }
  .brand-name { font-family: var(--nav); font-weight: 500; font-size: 17px; color: var(--ink); letter-spacing: 0.3px; }
  .main-nav { position: absolute; right: 112px; top: 60px; display: flex; gap: 34px; }
  .main-nav a { font-family: var(--nav); font-weight: 500; font-size: 16px; color: var(--ink); text-decoration: none; letter-spacing: 0.4px; }

  .hero-photo { position: absolute; left: 0; top: 135px; width: 1200px; height: 515px;
    background: linear-gradient(110deg, #8a949a 0%, #3f8fcf 28%, #cfe3ef 45%, #1d1d22 58%, #c2465e 70%, #e8e2a8 80%, #6d7073 100%); }
  .welcome-card { position: absolute; left: 112px; top: 393px; width: 368px; height: 335px; background: var(--red);
    color: var(--white); text-align: center; padding-top: 54px; }
  .welcome-card h2 { font-family: var(--head); font-weight: 600; font-size: 29px; }
  .welcome-card .welcome-name { font-family: var(--nav); font-weight: 500; font-size: 24px; margin-top: 20px; letter-spacing: 0.2px; }
  .welcome-card p { font-family: var(--body); font-size: 15.5px; line-height: 34px; margin: 47px auto 0; width: 330px; }

  .about { position: absolute; left: 0; top: 800px; width: 1200px; text-align: center; }
  .section-title { font-family: var(--head); font-weight: 500; font-size: 37px; color: var(--red); }
  .about p { font-family: var(--body); font-size: 15.5px; line-height: 34.5px; color: var(--text); width: 765px; margin: 24px auto 0; }
  .btn-outline { display: inline-block; margin-top: 38px; width: 160px; height: 52px; border: 2px solid var(--red);
    font-family: var(--head); font-weight: 500; font-size: 20px; color: var(--red); line-height: 48px; text-decoration: none; }

  .gallery-title { position: absolute; left: 0; top: 1172px; width: 1200px; text-align: center; }
  .tile { position: absolute; }
  .tile-feature { display: flex; align-items: center; justify-content: center; font-family: var(--head); font-weight: 500; font-size: 37px; color: var(--white); }

  .site-footer { position: absolute; left: 0; top: 2038px; width: 1200px; height: 343px; background: var(--black); color: var(--white); }
  .contact { position: absolute; left: 113px; top: 70px; font-family: var(--head); font-weight: 500; font-size: 19px; line-height: 47px; list-style: none; }
  .newsletter { position: absolute; left: 398px; top: 62px; width: 403px; text-align: center; }
  .newsletter h3 { font-family: var(--head); font-weight: 500; font-size: 32px; }
  .signup { margin-top: 37px; height: 48px; background: var(--white); display: flex; align-items: center; justify-content: space-between; padding: 0 17px; }
  .signup span { font-family: var(--head); font-size: 12.5px; color: #555; }
  .copyright { margin-top: 38px; font-family: var(--head); font-weight: 500; font-size: 12.5px; line-height: 28px; }
  .footer-nav { position: absolute; left: 967px; top: 68px; list-style: none; font-family: var(--head); font-weight: 500; font-size: 17px; line-height: 48px; }
</style>
</head>
<body>
<div class="page">
  <header class="site-header">
    <div class="brand"><span class="brand-name">QUIET HARBOR PRINTS</span></div>
    <nav class="main-nav">
      <a href="#">KÜNSTLER</a><a href="#">VERANSTALTUNGEN</a><a href="#">SHOP</a><a href="#">ABOUT US</a>
    </nav>
  </header>

  <div class="hero-photo" role="img" aria-label="Artist leaning over a large abstract painting in blue, pink and yellow on the studio floor"></div>
  <section class="welcome-card">
    <h2>Welcome To</h2>
    <div class="welcome-name">QUIET HARBOR PRINTS</div>
    <p>Sed ut perspiciatis unde omnis iste natus error sit voluptatem accusantium doloremque laudantium</p>
  </section>

  <section class="about">
    <h2 class="section-title">About Quiet Harbor Prints</h2>
    <p>Lorem ipsum dolor sit amet, consectetur adipiscing elit, sed do eiusmod tempor incididunt ut labore et dolore magna aliqua. Ut enim ad minim veniam, quis nostrud exercitation ullamco laboris nisi ut aliquip ex ea commodo consequat. Duis aute irure dolor in reprehenderit in voluptate velit esse cillum dolore eu fugiat nulla pariatur.</p>
    <a class="btn-outline" href="#">Learn More</a>
  </section>

  <h2 class="section-title gallery-title">Our Gallery</h2>

  <div class="tile" style="left:118px;top:1285px;width:307px;height:206px;background:radial-gradient(circle at 50% 40%,#d9564a 0%,#e7b07a 35%,#f1dcc0 70%)" role="img" aria-label="Colourful heart-shaped tree painting"></div>
  <div class="tile" style="left:445px;top:1285px;width:307px;height:206px;background:linear-gradient(120deg,#2c2a2c,#3f7c92 40%,#6b4a2a 75%,#2a1d14)" role="img" aria-label="Painter in a dim studio before a large canvas"></div>
  <div class="tile" style="left:771px;top:1285px;width:307px;height:206px;background:linear-gradient(180deg,#d7dbdc,#b9c3c6 55%,#2b2e30)" role="img" aria-label="Woman painting at an easel by a bright window"></div>

  <div class="tile" style="left:118px;top:1516px;width:195px;height:206px;background:linear-gradient(135deg,#b9584a,#e2373a 35%,#2fa0d8 65%,#f2b64a)" role="img" aria-label="Brush mixing bright paint on a palette"></div>
  <div class="tile tile-feature" style="left:337px;top:1516px;width:523px;height:206px;background:linear-gradient(180deg,#6a5a1a,#8a4a1c 55%,#3a3d8a)" role="img" aria-label="Painting of a wooden boat on a golden sea">Lorem Ipsum</div>
  <div class="tile" style="left:883px;top:1516px;width:195px;height:206px;background:linear-gradient(120deg,#cfd6de,#c84a35 45%,#4e79b8 80%)" role="img" aria-label="Hand applying thick paint to canvas"></div>

  <div class="tile" style="left:118px;top:1747px;width:307px;height:206px;background:linear-gradient(140deg,#e24a5a,#f0c33a 45%,#3c8fd0 75%,#f2d04a)" role="img" aria-label="Paintbrushes resting on colourful paint"></div>
  <div class="tile" style="left:445px;top:1747px;width:307px;height:206px;background:linear-gradient(180deg,#1c3c7a,#2a6fbf 50%,#e9b23a 85%,#1a2a5a)" role="img" aria-label="Fantasy painting of balloons rising over a glowing sky"></div>
  <div class="tile" style="left:771px;top:1747px;width:307px;height:206px;background:linear-gradient(120deg,#1b3f9a,#c0372e 45%,#2a7ac8 75%,#10245a)" role="img" aria-label="Portrait covered in bright paint colours"></div>

  <footer class="site-footer">
    <ul class="contact">
      <li>Hafenweg 7 20457</li>
      <li>Hamburg</li>
      <li>0171 5550 21 90</li>
      <li>info@quietharborprints.de</li>
    </ul>
    <div class="newsletter">
      <h3>Newsletter</h3>
      <div class="signup">
        <span>Enter Email Address</span>
        <svg width="22" height="12" viewBox="0 0 22 12" aria-hidden="true"><path d="M1 6h19M15 1l5 5-5 5" fill="none" stroke="#c0161f" stroke-width="1.6"/></svg>
      </div>
      <p class="copyright">@2024 Copyrights Quiet Harbor Prints<br>All Rights Reserved</p>
    </div>
    <ul class="footer-nav">
      <li>Künstler</li><li>Veranstaltungen</li><li>Shop</li><li>About Us</li>
    </ul>
  </footer>
</div>
</body>
</html>
```